Brightwave Exterior cleaning Logo

We need a new business card design, i would like to use our existing logo (attached).
Our logo on the left & a unique graphic design on the right of either a man holding a pressure washer gun & hose with a thumbs up or an image portraying dirt melting off a building or the two incorperated together, or something similar that represents exterior cleaning in progress, an image that shows/explains that we are exterior cleaners/pressure washers. Has to incorporate the zentrix & chatlane symbol perhaps in the bottom corners of the business card.
Existing business symbol on the back of the card with some blank lines for space to hand write quotes or job notes.
Industry/Entity Type
Exterior Cleaning
Contact Information for Business Card
Business mobile No. to be prominent (0472 918 346) Services provided listed as dot points. -Soft Washing -Pressure Washing - Solar Panel Cleaning - All General Exterior Cleaning. Email listed in fineprint (enquiries@tallowbrookwashworks.com.au). Owner Operator - Declan Morrow (this should also be added somewhere prominent). Residential & Comercial Cleaning.
Colors
Designer to choose colors to be used in the design.
Look and feel

```html
<!DOCTYPE html>
<html lang="en">
<head>
<meta charset="utf-8">
<title>Tallowbrook Washworks – Business Card</title>
<link rel="stylesheet" href="https://fonts.googleapis.com/css2?family=Roboto:wght@400;700&display=swap">
<style>
  :root {
    --bg: #3a3a3a;
    --card-white: #ffffff;
    --card-black: #121212;
    --brand-blue: #4a63b5;
    --ink-black: #111111;
    --ink-grey: #5c5c5c;
    --ink-light: #f2f2f2;
    --mark-grey: #8a8a8a;
  }
  * { box-sizing: border-box; margin: 0; padding: 0; }
  html, body {
    width: 1200px; height: 801px; overflow: hidden;
    background: var(--bg);
    font-family: "Roboto", Arial, sans-serif;
  }
  .stage { position: relative; width: 1200px; height: 801px; }

  .card {
    position: absolute; top: 236px;
    width: 540px; height: 330px;
    border-bottom: 3px solid var(--brand-blue);
  }
  .card--front { left: 45px; background: var(--card-white); }
  .card--back  { left: 615px; background: var(--card-black); }

  /* Front */
  .brand {
    position: absolute; left: 34px; top: 120px; width: 170px;
    display: flex; align-items: center; gap: 10px;
  }
  .brand__square { width: 16px; height: 16px; background: var(--brand-blue); flex: none; }
  .brand__name {
    color: var(--brand-blue); font-weight: 700; font-size: 19px;
    line-height: 1.15; text-transform: uppercase;
  }
  .divider {
    position: absolute; left: 222px; top: 70px;
    width: 2px; height: 120px; background: var(--brand-blue);
  }
  .contact { position: absolute; left: 244px; top: 64px; }
  .contact__name {
    color: var(--brand-blue); font-weight: 700; font-size: 22px;
    text-transform: uppercase; letter-spacing: 0.2px;
  }
  .contact__role { color: var(--ink-grey); font-size: 13px; margin: 3px 0 16px 12px; }
  .contact__line {
    display: flex; align-items: center; gap: 7px;
    color: var(--ink-grey); font-size: 12px; margin: 0 0 5px 12px;
  }
  .contact__line--phone { color: var(--brand-blue); font-weight: 700; font-size: 15px; }
  .contact__line svg { width: 12px; height: 12px; flex: none; }
  .tagline {
    position: absolute; left: 244px; bottom: 48px;
    color: var(--ink-grey); font-size: 14px;
  }

  /* Back */
  .back-brand {
    position: absolute; left: 0; right: 0; top: 108px;
    display: flex; justify-content: center; align-items: center; gap: 12px;
  }
  .back-brand__square { width: 22px; height: 22px; background: var(--mark-grey); }
  .back-brand__name {
    color: var(--mark-grey); font-weight: 700; font-size: 24px; text-transform: uppercase;
  }
  .services {
    position: absolute; left: 0; right: 0; bottom: 34px;
    text-align: center; color: var(--ink-light); font-size: 14px;
  }
  .services__dot { color: var(--brand-blue); margin: 0 5px; }
</style>
</head>
<body>
<main class="stage">

  <section class="card card--front" aria-label="Business card front">
    <div class="brand">
      <span class="brand__square"></span>
      <span class="brand__name">Tallowbrook Washworks</span>
    </div>
    <div class="divider"></div>
    <div class="contact">
      <p class="contact__name">Declan Morrow</p>
      <p class="contact__role">Owner Operator</p>
      <p class="contact__line contact__line--phone">
        <svg viewBox="0 0 24 24" fill="currentColor"><path d="M6.6 10.8a15 15 0 006.6 6.6l2.2-2.2a1 1 0 011-.25 11.4 11.4 0 003.6.57 1 1 0 011 1V20a1 1 0 01-1 1A17 17 0 013 4a1 1 0 011-1h3.5a1 1 0 011 1c0 1.25.2 2.45.57 3.57a1 1 0 01-.25 1z"/></svg>
        0472 918 346
      </p>
      <p class="contact__line">
        <svg viewBox="0 0 24 24" fill="var(--brand-blue)"><path d="M2 5h20v14H2z" opacity=".9"/><path d="M2 5l10 8 10-8" stroke="#fff" stroke-width="1.8" fill="none"/></svg>
        enquiries@tallowbrookwashworks.com.au
      </p>
      <p class="contact__line">
        <svg viewBox="0 0 24 24" fill="none" stroke="var(--brand-blue)" stroke-width="2"><circle cx="12" cy="12" r="9"/><path d="M3 12h18M12 3c3 3 3 15 0 18M12 3c-3 3-3 15 0 18"/></svg>
        www.tallowbrookwashworks.com.au
      </p>
    </div>
    <p class="tagline">Residential &amp; Comercial Cleaning</p>
  </section>

  <section class="card card--back" aria-label="Business card back">
    <div class="back-brand">
      <span class="back-brand__square"></span>
      <span class="back-brand__name">Tallowbrook</span>
    </div>
    <p class="services">
      Soft Washing<span class="services__dot">•</span>Pressure Washing<span class="services__dot">•</span>Solar Panel Cleaning<span class="services__dot">•</span>All General Exterior Cleaning
    </p>
  </section>

</main>
</body>
</html>
```